International Reinsurance Business Platform Needs a PowerPoint Design

We need a powerpoint design for a new company based in Bermuda. We have created a platform to facilitate the incorporation and creation of off-shore reinsurance companies, primarily offered to asset managers to generate permanent capital at a fraction of the costs typically required by such a venture. We have no preference as to the color scheme, but would like for the final design to communicate professionalism, simplicity and elegance.
We have uploaded a very rudimentary draft (far from what we want), and welcome you to recreate a single page from it (it can be a combination of two pages into one; preferably something complicated enough to showcase the potential of your idea). From there, we will pick from the better submissions (of that single page) and work from there.
High-income asset managers
Business

```html
<!DOCTYPE html>
<html lang="en">
<head>
<meta charset="utf-8">
<title>Each faced significant hurdles</title>
<link rel="stylesheet" href="https://fonts.googleapis.com/css2?family=Carlito:ital,wght@0,400;0,700;1,400;1,700&display=swap">
<style>
  :root {
    --gold: #ebba00;
    --gold-text: #d9a800;
    --gold-deep: #c9a000;
    --rule-dark: #4a4a4a;
    --rule-mid: #7a7a7a;
    --ink: #1b1b1b;
    --paper: #ffffff;
    --bullet: #f0a500;
  }
  * { margin: 0; padding: 0; box-sizing: border-box; }
  html, body { width: 1200px; height: 900px; overflow: hidden; background: var(--paper); }
  body { font-family: "Carlito", "Calibri", sans-serif; color: var(--ink); }

  .slide { position: relative; width: 1200px; height: 900px; overflow: hidden; background: var(--paper); }

  .header-band { position: absolute; left: 0; top: 0; width: 1200px; height: 95px; background: var(--gold); }
  .header-rule {
    position: absolute; left: 0; top: 95px; width: 1200px; height: 10px;
    background: repeating-linear-gradient(135deg, var(--rule-dark) 0 2px, var(--rule-mid) 2px 4px);
  }
  .slide-title {
    position: absolute; left: 42px; top: 24px;
    font-size: 34px; font-weight: 700; color: var(--paper); letter-spacing: 0.2px;
  }
  .brand-name {
    position: absolute; right: 36px; top: 18px;
    font-size: 56px; font-weight: 400; color: var(--paper); letter-spacing: 1px; line-height: 1;
  }

  .backdrop-texture {
    position: absolute; left: 380px; top: 105px; width: 820px; height: 700px;
    background: radial-gradient(ellipse at 85% 30%, rgba(200,200,200,0.35) 0%, rgba(225,225,225,0.2) 40%, rgba(255,255,255,0) 70%);
  }

  .hurdle-list { position: absolute; left: 50px; top: 219px; list-style: none; }
  .hurdle {
    display: flex; align-items: center; height: 89px;
    font-size: 25px; font-weight: 700; color: var(--ink);
  }
  .hurdle:first-child { height: 48px; margin-bottom: 41px; }
  .hurdle-icon { width: 48px; height: 48px; margin-right: 28px; flex: none; }
  .accent { font-style: italic; font-weight: 400; color: var(--gold-text); font-size: 31px; margin: 0 4px; }

  .closing-line {
    position: absolute; left: 125px; top: 690px;
    font-size: 46px; font-weight: 400; color: var(--gold-deep); letter-spacing: 0.3px;
  }

  .footer-rule {
    position: absolute; left: 0; top: 806px; width: 1200px; height: 12px;
    background: repeating-linear-gradient(135deg, var(--rule-mid) 0 2px, #a8a8a8 2px 4px);
  }
  .footer-band { position: absolute; left: 0; top: 818px; width: 1200px; height: 82px; background: var(--gold); }
  .page-number {
    position: absolute; right: 44px; top: 844px;
    font-size: 26px; font-weight: 700; color: var(--paper);
  }
</style>
</head>
<body>
<main class="slide">
  <div class="backdrop-texture" role="img" aria-label="Faint dotted texture fading across the slide background"></div>

  <div class="header-band"></div>
  <div class="header-rule"></div>
  <h1 class="slide-title">Each faced significant hurdles</h1>
  <div class="brand-name">Verholt Capital</div>

  <ul class="hurdle-list">
    <li class="hurdle">
      <svg class="hurdle-icon" viewBox="0 0 48 48" aria-hidden="true"><circle cx="24" cy="24" r="22" fill="#e6e6e6"/><circle cx="24" cy="24" r="19" fill="#fff"/><circle cx="24" cy="24" r="15.5" fill="var(--bullet)"/><path d="M16 24h15M25 18l6 6-6 6" fill="none" stroke="#fff" stroke-width="3" stroke-linecap="round" stroke-linejoin="round"/></svg>
      Had to hire marquee reinsurance teams
    </li>
    <li class="hurdle">
      <svg class="hurdle-icon" viewBox="0 0 48 48" aria-hidden="true"><circle cx="24" cy="24" r="22" fill="#e6e6e6"/><circle cx="24" cy="24" r="19" fill="#fff"/><circle cx="24" cy="24" r="15.5" fill="var(--bullet)"/><path d="M16 24h15M25 18l6 6-6 6" fill="none" stroke="#fff" stroke-width="3" stroke-linecap="round" stroke-linejoin="round"/></svg>
      Reinsurace teams received<span class="accent">large</span>guarantees
    </li>
    <li class="hurdle">
      <svg class="hurdle-icon" viewBox="0 0 48 48" aria-hidden="true"><circle cx="24" cy="24" r="22" fill="#e6e6e6"/><circle cx="24" cy="24" r="19" fill="#fff"/><circle cx="24" cy="24" r="15.5" fill="var(--bullet)"/><path d="M16 24h15M25 18l6 6-6 6" fill="none" stroke="#fff" stroke-width="3" stroke-linecap="round" stroke-linejoin="round"/></svg>
      Had to raise<span class="accent">at least</span>$250 million of capital
    </li>
    <li class="hurdle">
      <svg class="hurdle-icon" viewBox="0 0 48 48" aria-hidden="true"><circle cx="24" cy="24" r="22" fill="#e6e6e6"/><circle cx="24" cy="24" r="19" fill="#fff"/><circle cx="24" cy="24" r="15.5" fill="var(--bullet)"/><path d="M16 24h15M25 18l6 6-6 6" fill="none" stroke="#fff" stroke-width="3" stroke-linecap="round" stroke-linejoin="round"/></svg>
      <span class="accent" style="margin-left:0">Large</span>busted deal, startup, and fixed costs
    </li>
    <li class="hurdle">
      <svg class="hurdle-icon" viewBox="0 0 48 48" aria-hidden="true"><circle cx="24" cy="24" r="22" fill="#e6e6e6"/><circle cx="24" cy="24" r="19" fill="#fff"/><circle cx="24" cy="24" r="15.5" fill="var(--bullet)"/><path d="M16 24h15M25 18l6 6-6 6" fill="none" stroke="#fff" stroke-width="3" stroke-linecap="round" stroke-linejoin="round"/></svg>
      Redirection of resources for<span class="accent">1 to 2 year</span>
    </li>
  </ul>

  <p class="closing-line">Many more have tried and failed</p>

  <div class="footer-rule"></div>
  <div class="footer-band"></div>
  <div class="page-number">2</div>
</main>
</body>
</html>
```